Systems and Technology Consultants - Website

Design & Build a website for a new company which operates in the Systems and Technology space for Transportation, Government and Commercial sectors.

Overall design should be minimalist in nature.
Should also have a feed that provides news and event updates on the main page.
Logo has already been awarded and should be incorporated into the site.

We like the overall layout, functionality and simplicity of the below sites. Submitted designs could be similar to or a combination of the aspects on these sites, or perhaps a whole different concept - we are open to new ideas.
Norvique.com
Teblo.it

Update 1 Dated 27 May 2014

All I am moving away from the Teblo.it website and would like it to be more aligned with Norvique.com not only in layout but in functionality. I will be extending the deadline of this design brief for two weeks to incorporate additional requirements and will add addtional funding to the project.

Apologies for not having more information available to provide but with so many submissions its getting confusing.

Thanks Derek

Please note that the brief has been updated and the deadline has been extended.

Important: We will need two language versions of the website, English and Arabic; the website is hosted on HostPelican

Hello All, Thank you for your submissions. We have narrowed it down to the final 6 designers and I just wanted to take a moment and provide a bit of feedback regarding the concepts that we like and the modifications we are looking for. First, let me mention some of the design functions we like. - At the top of the homepage we really like the "region" or "language" tab so that the website can be viewed in both English and Arabic. - We like the homepage to have clear color variation so that the different sections of the homepage are distinct. Additionally, we like the bottom portion of the homepage to be in red. We feel that draws attention to our contact information. Again, we would like the colors to integrate black, gray-scale, red, etc. - Having a search tab at the top of the home page, or integrated into the main image, so that the site is easy to navigate. - We especially like the main image to have the scrolling tabs at the bottom so it is easy to browse the services offered (Consultancy, Solutions Architecture, Masters Systems Integration, Independent Design Review). - In regards to the services offered tab we really like the idea that a few people presented that have the outside of our logo with an icon in the middle of consultancy, solutions, etc., etc. Secondly, as mentioned in our brief we really enjoy the design of norvique site. Specially, we enjoy the strong iconic images they use, the way the tabs at the top scroll easily, and contact us page that generates an email. Lastly, I've included some photos of the concept we have been working on. What we are trying to demonstrate is how our company offers a range of services that are essentially linked together. We provide individual services that when combined present the full service package. We would like this concept to be integrated into the over concept of our website. Please feel free to ask for clarification of any of the above points or contact us if you have any additional questions. We appreciate all of your hard work and are very excited to see the updated designs. Best, Marta Vennick Quelbrant Senior Program Manager marta.vennick@quelbrant-example.com

Industry/Entity Type

Government

Font styles to use
Serif
Sans Serif

Requirements
Must have
• Must work on/adapt to various/mobile devices (responsive)
Must be simple and straightforward
Colors should be in line/matching with logo
2 language versions: English and Arabic (no Thai)
Services should be the first group/row of items after/below the main image
Note: the website will be hosted by hostpelican
Nice to have
• Submit feedback form
What's New section
The banner at the bottom of the site should not be too large; we would like a narrow one more
It would be nice if the header/top banner (with Home, About, etc. tabs) could stay in place as you scroll down (like Norvique and Chatterloop)
We will likely only use one image with a Company slogan on the Home page rather than a carousel of images to rotate through
Should not have
• This is the existing website: http://www.quelbrant-example.org
We do not like the animation, the way the banner icons/titles bounce
Not simple enough, we don't like the functionality or how pages load so slowly
We do not like the logo centered - it should be at the left
The banner and its tabs should not be towards the right, we would like them to be centered, to go all the way across and to be below the logo

```html
<!DOCTYPE html>
<html lang="en">
<head>
<meta charset="utf-8">
<title>Quelbrant</title>
<link href="https://fonts.googleapis.com/css2?family=Roboto:ital,wght@0,300;0,400;0,500;0,700;1,400&display=swap" rel="stylesheet">
<style>
:root{
  --red:#e2202a;
  --charcoal:#333333;
  --ink:#222222;
  --muted:#777777;
  --soft:#f4f4f4;
  --line:#e6e6e6;
  --white:#ffffff;
}
*{box-sizing:border-box;margin:0;padding:0}
html,body{width:806px;height:1200px;overflow:hidden}
body{font-family:'Roboto',sans-serif;background:var(--white);color:var(--ink);position:relative}
.abs{position:absolute}

.topbar{left:0;top:0;width:806px;height:17px;background:var(--charcoal)}
.lang{right:150px;top:4px;font-size:7px;color:#ddd;display:flex;align-items:center;gap:4px}
.lang .flag{width:8px;height:5px;background:#3b4fa0;border:1px solid #c33}
.lang .caret{width:0;height:0;border-left:3.5px solid transparent;border-right:3.5px solid transparent;border-top:4px solid #ddd;margin-left:4px}

.header{left:0;top:17px;width:806px;height:59px;background:var(--white)}
.brand{left:153px;top:38px;display:flex;align-items:center;gap:6px}
.brand .dot{width:10px;height:10px;border-radius:50%;background:var(--red)}
.brand .name{font-size:14px;font-weight:500;color:var(--ink);line-height:14px}
.nav a{position:absolute;top:0;height:59px;line-height:59px;font-size:6px;color:#444;text-decoration:none;white-space:nowrap}
.nav a.active{background:var(--red);color:var(--white);width:34px;text-align:center}
.search{left:644px;top:42px;width:10px;height:10px;background:var(--red)}
.search svg{display:block}

.hero{left:0;top:76px;width:806px;height:212px;background:radial-gradient(ellipse at 50% 30%,#7a1a1f 0%,#3a2a2a 40%,#1c1c1e 80%)}
.hero h1{position:absolute;left:0;right:0;top:72px;text-align:center;font-size:20px;font-weight:700;color:var(--white)}
.hero p{position:absolute;left:190px;right:190px;top:108px;text-align:center;font-size:10.3px;font-weight:300;line-height:15.5px;color:#f2f2f2}

.section-title{position:absolute;left:0;right:0;text-align:center;font-size:12px;font-weight:500;color:var(--ink)}
.underline{position:absolute;left:382px;width:42px;height:2px;background:var(--red)}

.service-line{left:210px;top:383px;width:390px;height:2px;background:var(--line)}
.service{width:50px;height:50px;border-radius:50%;background:var(--white);border:2px solid var(--line);top:359px}
.service svg{position:absolute;left:14px;top:14px}
.service-label{top:421px;width:80px;text-align:center;font-size:7px;color:var(--muted)}

.news-band{left:0;top:454px;width:806px;height:252px;background:var(--soft)}
.news-card{top:524px;width:112px}
.news-card .thumb{height:70px}
.news-card h3{font-size:7.5px;font-weight:500;text-align:center;margin-top:7px;color:#333}
.news-card p{font-size:5.6px;line-height:7.7px;color:var(--muted);text-align:center;margin-top:8px;padding:0 2px}
.btn{display:block;background:var(--red);color:var(--white);font-size:5.8px;font-weight:700;text-align:center;border-radius:2px}
.news-card .btn{width:42px;height:15px;line-height:15px;margin:19px auto 0}

.event{top:776px;width:170px}
.event .date{position:absolute;left:-29px;top:2px;width:42px;height:42px;border-radius:50%;background:#f1f1f1;text-align:center}
.event .date span{display:block;font-size:6.5px;color:#999;margin-top:11px}
.event .date b{display:block;font-size:10px;font-weight:700;color:#333}
.event h4{font-size:7.5px;font-weight:500;margin-left:30px;color:#333}
.event p{font-size:5.6px;line-height:7.7px;color:var(--muted);margin-left:30px;margin-top:5px;text-align:justify;width:102px}

.quote-band{left:0;top:845px;width:806px;height:109px;background:linear-gradient(90deg,#a81e26,#c8252e 50%,#a81e26)}
.portrait{left:241px;top:870px;width:60px;height:60px;border-radius:50%;border:2px solid var(--white);background:linear-gradient(#e8e8e8,#8a8a8a)}
.quote{left:326px;top:877px;width:240px;font-size:7.4px;font-weight:400;font-style:italic;line-height:11px;color:var(--white)}
.qmark{font-size:16px;font-weight:700;color:var(--white);line-height:16px}

.field{background:#f2f2f2;font-size:7.2px;color:#888;padding:6px 8px}
.send{left:370px;top:1097px;width:67px;height:16px;line-height:16px}

.footer{left:0;top:1138px;width:806px;height:62px;background:var(--charcoal)}
.footer small{position:absolute;left:153px;top:27px;font-size:6.6px;color:#ccc}
.social{top:1164px;width:10px;height:10px;border-radius:50%;background:#bbb}
</style>
</head>
<body>

<div class="abs topbar">
  <div class="abs lang"><span class="flag"></span>English<span class="caret"></span></div>
</div>

<header class="abs header"></header>
<div class="abs brand"><span class="dot"></span><span class="name">Quelbrant</span></div>
<nav class="abs nav" style="left:0;top:17px;width:806px;height:59px">
  <a class="active" style="left:361px">HOME</a>
  <a style="left:403px">BUSINESS UNIT</a>
  <a style="left:462px">SERVICES</a>
  <a style="left:504px">ABOUT US</a>
  <a style="left:547px">LOCATIONS</a>
  <a style="left:593px">CONTACT US</a>
</nav>
<div class="abs search">
  <svg width="10" height="10" viewBox="0 0 10 10"><circle cx="4.3" cy="4.3" r="2.2" fill="none" stroke="#fff" stroke-width="1"/><line x1="6" y1="6" x2="8" y2="8" stroke="#fff" stroke-width="1.2"/></svg>
</div>

<section class="abs hero" role="img" aria-label="Blurred close-up of red network cables in a server rack">
  <h1>SYSTEM PROFESSIONALS</h1>
  <p>We provide construction management, engineering, design services and turn-key solutions for technical systems.</p>
</section>

<h2 class="section-title" style="top:311px">WHAT WE DO</h2>
<div class="underline" style="top:331px"></div>
<div class="abs service-line"></div>
<div class="abs service" style="left:174px"><svg width="18" height="18" viewBox="0 0 18 18"><circle cx="9" cy="6" r="3.5" fill="#444"/><path d="M3 15c0-4 3-5 6-5s6 1 6 5z" fill="#444"/></svg></div>
<div class="abs service" style="left:276px"><svg width="18" height="18" viewBox="0 0 18 18"><circle cx="9" cy="9" r="5" fill="none" stroke="#444" stroke-width="3" stroke-dasharray="2.5 1.4"/><circle cx="9" cy="9" r="1.8" fill="#444"/></svg></div>
<div class="abs service" style="left:377px"><svg width="18" height="18" viewBox="0 0 18 18"><path d="M4 4l10 10M14 4L4 14" stroke="#444" stroke-width="2.2" stroke-linecap="round"/></svg></div>
<div class="abs service" style="left:480px"><svg width="18" height="18" viewBox="0 0 18 18"><circle cx="9" cy="9" r="5" fill="none" stroke="#444" stroke-width="1.6" stroke-dasharray="6 2"/><circle cx="9" cy="4" r="1.3" fill="#444"/><circle cx="5" cy="12" r="1.3" fill="#444"/><circle cx="13" cy="12" r="1.3" fill="#444"/></svg></div>
<div class="abs service" style="left:582px"><svg width="18" height="18" viewBox="0 0 18 18"><rect x="4" y="3" width="10" height="3" fill="#444"/><rect x="4" y="7.5" width="10" height="3" fill="#444"/><rect x="4" y="12" width="10" height="3" fill="#444"/></svg></div>
<div class="abs service-label" style="left:159px">Consulting</div>
<div class="abs service-label" style="left:261px">Engineering</div>
<div class="abs service-label" style="left:362px">Construction</div>
<div class="abs service-label" style="left:465px">Operations</div>
<div class="abs service-label" style="left:567px">Maintenance</div>

<section class="abs news-band"></section>
<h2 class="section-title" style="top:477px">WHAT’S NEW</h2>
<div class="underline" style="top:497px"></div>

<article class="abs news-card" style="left:153px">
  <div class="thumb" role="img" aria-label="Building plans with a tape measure, hammer and hard hat" style="background:linear-gradient(135deg,#c9d3e6,#e8e8ef 55%,#e6b93a)"></div>
  <h3>Lorem Ipsum</h3>
  <p>Lorem ipsum dolor sit amet, consectetur adipisicing elit, sed do eiusmod tempor incididunt ut labore et dolore magna aliqua.</p>
  <a class="btn">Read more</a>
</article>
<article class="abs news-card" style="left:282px">
  <div class="thumb" role="img" aria-label="Audience seated in a conference hall" style="background:linear-gradient(#7a1a18,#b8322a 60%,#3a1a14)"></div>
  <h3>Lorem Ipsum</h3>
  <p>Lorem ipsum dolor sit amet, consectetur adipisicing elit, sed do eiusmod tempor incididunt ut labore et dolore magna aliqua.</p>
  <a class="btn">Read more</a>
</article>
<article class="abs news-card" style="left:411px">
  <div class="thumb" role="img" aria-label="Rows of illuminated data centre server racks" style="background:linear-gradient(90deg,#0a1f8a,#2a6ae0 50%,#0a1f8a)"></div>
  <h3>Lorem Ipsum</h3>
  <p>Lorem ipsum dolor sit amet, consectetur adipisicing elit, sed do eiusmod tempor incididunt ut labore et dolore magna aliqua.</p>
  <a class="btn">Read more</a>
</article>
<article class="abs news-card" style="left:541px">
  <div class="thumb" role="img" aria-label="Visitors at a colourful trade fair exhibition stand" style="background:linear-gradient(#8a8a86,#9ac23a 55%,#5a6a7a)"></div>
  <h3>Lorem Ipsum</h3>
  <p>Lorem ipsum dolor sit amet, consectetur adipisicing elit, sed do eiusmod tempor incididunt ut labore et dolore magna aliqua.</p>
  <a class="btn">Read more</a>
</article>

<h2 class="section-title" style="top:729px">EVENT UPDATES</h2>
<div class="underline" style="top:749px"></div>
<div class="abs event" style="left:174px">
  <div class="date"><span>31 MAY</span><b>2014</b></div>
  <h4>Lorem Ipsum Dolor Sit Amet</h4>
  <p>Lorem ipsum dolor sit amet, consectetur adipisicing elit, sed do eiusmod tempor incididunt ut labore et dolore magna aliqua.</p>
</div>
<div class="abs event" style="left:343px">
  <div class="date"><span>18 MAY</span><b>2014</b></div>
  <h4>Lorem Ipsum Dolor Sit Amet</h4>
  <p>Lorem ipsum dolor sit amet, consectetur adipisicing elit, sed do e iusmod tempor incididunt ut labore et dolore magna aliqua.</p>
</div>
<div class="abs event" style="left:513px">
  <div class="date"><span>06 MAY</span><b>2014</b></div>
  <h4>Lorem Ipsum Dolor Sit Amet</h4>
  <p>Lorem ipsum dolor sit amet, consectetur adipisicing elit, sed do eiusmod tempor incididunt ut labore et dolore magna aliqua.</p>
</div>

<section class="abs quote-band"></section>
<div class="abs portrait" role="img" aria-label="Portrait photo of a company representative"></div>
<span class="abs qmark" style="left:335px;top:873px">”</span>
<blockquote class="abs quote"><span style="display:inline-block;width:32px"></span>Lorem ipsum dolor sit amet, consectetur adipisicing elit, sed do eiusmod tempor incididunt ut labore et dolore magna aliqua.Lorem ipsum dolor sit amet, consectetur adipisicing elit, sed do eiusmod tempor incididunt ut labore et dolore magna aliqua.</blockquote>
<span class="abs qmark" style="left:458px;top:913px">“</span>

<h2 class="section-title" style="top:978px">GET IN TOUCH</h2>
<div class="abs field" style="left:242px;top:1026px;width:106px;height:20px">Name</div>
<div class="abs field" style="left:242px;top:1050px;width:106px;height:20px">Email</div>
<div class="abs field" style="left:353px;top:1026px;width:212px;height:44px">Message</div>
<a class="abs btn send">Send Message</a>

<footer class="abs footer"><small>Quelbrant © 2014 , All Rights Reserved</small></footer>
<span class="abs social" style="left:614px"></span>
<span class="abs social" style="left:629px"></span>
<span class="abs social" style="left:643px"></span>

</body>
</html>
```